New Business Card Design for Manufacturing

We are an engineering/manufacturing company that offers Advanced machining/assembly/engineering services, as well as innovative products for the heavy duty engine cooling markets.

We are looking to get a new business card designed that is clean and modern looking, but still fits the wide range of technical/skilled work we do.

- We hope to use this design as the base for other design work in new Presentations, web, and print work.

Industry/Entity Type

Engineering

Contact Information for Business Card

Our preferred color of blue is (RGB) 22/71/159 but can vary slightly from that color. Our content will be our Logo and full company name (Vantrell Forge Works, Inc.), company address, name, job title, phone number with extension, cell number, fax number, website, and email address on the cards.
We'd like the full company name next to the logo, but we are open to other interpretations of that layout.
Preferably, we would like the back side to be clean with just our logo, and the front to contain all of the contact information.

Colors
2f74b4
0355a3
85abd2

Requirements
Must have
• - Logo, company name, needed content - We are open to interpretation beyond that.
• - Standard size business card.
• - Horizontal orientation.
• - Enough space for lengthy names / job titles (for example, a job title could read "Directory of Human Resources" or "V.P. of Governmental Affairs"). We need this to look clean, whether the title be short (CEO) or long (as described above).

```html
<!DOCTYPE html>
<html lang="en">
<head>
<meta charset="utf-8">
<title>Vantrell Forge Works — Business Card</title>
<link rel="stylesheet" href="https://fonts.googleapis.com/css2?family=Montserrat:wght@400;500;700;800&display=swap">
<style>
  :root {
    --brand-blue: #0f55a6;
    --brand-blue-deep: #0a4a94;
    --steel-grey: #8a8d91;
    --ink: #4a4c50;
    --paper: #ffffff;
    --stage: #2b2b2d;
  }
  * { box-sizing: border-box; margin: 0; padding: 0; }
  html, body { width: 1200px; height: 900px; overflow: hidden; }
  body {
    background: var(--stage);
    font-family: "Montserrat", Arial, sans-serif;
    position: relative;
  }
  .card {
    position: absolute;
    left: 280px;
    width: 640px;
    height: 366px;
    border-radius: 22px;
    overflow: hidden;
  }
  /* Back side */
  .card-back {
    top: 40px;
    background: var(--brand-blue);
  }
  .card-back .map-area {
    position: absolute;
    left: 80px; top: 20px;
    width: 480px; height: 260px;
    border-radius: 50%;
    background: radial-gradient(ellipse at center, rgba(255,255,255,0.06), rgba(255,255,255,0) 70%);
  }
  .card-back .wordmark {
    position: absolute;
    left: 0; right: 0; top: 118px;
    text-align: center;
    color: var(--paper);
    font-weight: 800;
    font-size: 36px;
    line-height: 1.15;
    letter-spacing: 0.5px;
    text-transform: uppercase;
  }
  .card-back .web {
    position: absolute;
    left: 0; right: 0; bottom: 36px;
    text-align: center;
    color: var(--paper);
    font-size: 13px;
    letter-spacing: 0.3px;
  }
  /* Front side */
  .card-front {
    top: 454px;
    background: var(--paper);
  }
  .card-front .waves {
    position: absolute; left: 0; top: 0;
    width: 640px; height: 366px;
  }
  .card-front .wordmark {
    position: absolute;
    left: 40px; top: 104px;
    width: 260px;
    color: var(--brand-blue);
    font-weight: 800;
    font-size: 26px;
    line-height: 1.15;
    text-transform: uppercase;
  }
  .card-front .divider {
    position: absolute;
    left: 320px; top: 82px;
    width: 1px; height: 170px;
    background: var(--steel-grey);
  }
  .contact {
    position: absolute;
    left: 340px; top: 84px;
    color: var(--ink);
  }
  .contact .person-name {
    color: var(--brand-blue);
    font-weight: 700;
    font-size: 21px;
    line-height: 1.1;
  }
  .contact .person-title {
    font-size: 12px;
    margin-top: 5px;
  }
  .contact .address {
    font-size: 13px;
    line-height: 1.55;
    margin-top: 9px;
  }
  .contact .lines {
    list-style: none;
    margin-top: 4px;
    font-size: 13px;
  }
  .contact .lines li {
    display: flex;
    align-items: center;
    gap: 8px;
    line-height: 20px;
  }
  .contact .lines svg { width: 12px; height: 12px; fill: var(--brand-blue); flex: none; }
  .card-front .web {
    position: absolute;
    right: 44px; bottom: 18px;
    color: var(--paper);
    font-size: 13px;
    letter-spacing: 0.3px;
  }
</style>
</head>
<body>

<section class="card card-back" aria-label="Card back">
  <div class="map-area" role="img" aria-label="Faint world map in the background"></div>
  <p class="wordmark">Vantrell<br>Forge Works</p>
  <p class="web">www.vantrellforge.com</p>
</section>

<section class="card card-front" aria-label="Card front">
  <svg class="waves" viewBox="0 0 640 366" aria-hidden="true">
    <path d="M0,226 C200,246 380,292 640,296 L640,366 L0,366 Z" fill="var(--steel-grey)"/>
    <path d="M0,236 C200,256 380,302 640,306 L640,366 L0,366 Z" fill="var(--paper)"/>
    <path d="M0,244 C200,264 380,310 640,314 L640,366 L0,366 Z" fill="var(--brand-blue)"/>
  </svg>

  <p class="wordmark">Vantrell Forge Works, Inc.</p>
  <div class="divider"></div>

  <div class="contact">
    <p class="person-name">Marcus Ellory</p>
    <p class="person-title">President</p>
    <p class="address">Street Name Avenue, Suite 100<br>State, Zip Code, Country</p>
    <ul class="lines">
      <li><svg viewBox="0 0 12 12"><path d="M2.5 0.8 L4.4 3 L3.4 4.3 C4 5.8 5.5 7.3 7.4 8.2 L8.7 7.2 L11 9.1 L9.8 11.2 C5 11 0.9 6.8 0.6 2 Z"/></svg>+000.000.00 00</li>
      <li><svg viewBox="0 0 12 12"><path d="M3 0 H9 A1 1 0 0 1 10 1 V11 A1 1 0 0 1 9 12 H3 A1 1 0 0 1 2 11 V1 A1 1 0 0 1 3 0 Z M3.3 1.5 V9 H8.7 V1.5 Z M5.3 9.8 H6.7 V11 H5.3 Z"/></svg>+000.000.00 00</li>
      <li><svg viewBox="0 0 12 12"><path d="M3 0 H9 V3 H3 Z M0.5 3.8 H11.5 V8.5 H9.5 V7 H2.5 V8.5 H0.5 Z M3 7.8 H9 V12 H3 Z"/></svg>+000.000.00 00</li>
      <li><svg viewBox="0 0 12 12"><path d="M0 2 H12 V10 H0 Z M1 3 V3.4 L6 6.8 L11 3.4 V3 Z"/></svg>www.vantrellforge.com</li>
    </ul>
  </div>

  <p class="web">www.vantrellforge.com</p>
</section>

</body>
</html>
```